Nutritional & Gastrointestinal Health Consulting Service-Website design

We need a website design for a new health consulting service called "Bright Vale" based in Perth, Australia.

We will be providing consulting services in the areas of:
1) Nutrition and Diet
2) Gastrointestinal Health (which means stomach & digestive system related health)

These consulting services will be provided by an Accredited Dietitian and a Paediatric Gastroenterologist.

We are open to creative ideas in terms of design, layout, fonts and colours. We also would love to see images of nature in the backdrop with families (adults with kids) having a good time, fresh fruits and vegetables displayed in a farmer's market or supermarket. 2 or 3 images should be sufficient. We would also definitely want our logo somewhere in the main page of website. The logo file is also attached. Please have a look at a website's design that we really liked. We would love to see designs inspired by that style. The website details are in the in the "nice to have priorities" section of this project brief.

We also would be looking at website designers with software coding skills so that if we like the design we can go ahead with the next step of coding.

The website design should communicate the purpose of the website and at the same time be simple, elegant and unique/eye-catching.

We look forward to receiving creative ideas for our website from you all. Good luck!

More details have been added to our project- for example: Logo, fonts style, must haves etc etc. Please view the updated project brief. Looking forward to receiving your fantastic ideas for our website. Thanking you

Hi, I have updated the colour preference. Will add the content preferences tomorrow. thanks

Hello all, I have now added a LOT more content to what we want in our website. It is very much in detail, so please carefully have a read through the entire project brief. If you have any questions write back to me and I will try to respond as quickly as I can. Last few days were busy so couldn't respond quickly to all of you who had send me designs/queries/questions. Thank you for your patience. I look forward to receiving fantastic designs from you all. Good Luck :-)

Target Market(s)

Adults based in western speaking countries aged 18 to 60 years

Industry/Entity Type

Software

Font styles to use
Sans Serif
Script

Colors
faa54b
acd036

Requirements
Must have
• The website must have the MAIN logo file attached. I have attached 3 files: 1) MAIN logo; 2) supplementary logo A ; 3) supplementary logo B

I have selected 2 colours from the colour scheme (see below)-(as the colour of our logo is that).
However we would also like to see LIGHT CHOCOLATE BROWN or CHOCOLATE BROWN colour used as the background colour of the website
Preferred WEBSITE CONTENT:
1) HOME PAGE:
Content required=
--Company Logo
--Dr Dorian Pelham
Paediatric Gastroenterologist & Hepatologist
-Marla Pelham.
Dietitian & Nutritionist
--Website Menu (either listed horizontally or vertically):
Once clicked on each name:

Under each of the Website Menu items we want the following Headings to be added

2) ABOUT US page:
Sub-heading under this: Qualification, Skills, Special Interest

3) SERVICES
DORIAN'S PAGE: Individual Consultation, Endoscopy procedures
Individual Consultation, Group Based Services, Food Diary, Food & Symptom Diary

4) FEES & REBATE: Content as below:
Please Note: Payment of full fees is required at the time of consultation and procedures. 48 hours notice is required for cancellation of appointments/non-attendance. Failure to provide this may result in a fee being incurred. Please call reception to find out the amount of fee charged for cancellation of appointments/non-attendance.
headings are:
Paediatric Gastroenterology:
Dorian's pge
Individual Consultation - Initial (upto 30 mins):
Review Consultation (upto 15 mins):
Endoscopy procedures - No Gap fees charged. Fees will be billed directly to Vitacover. If any queries, please contact reception.

marla's pge
sub heading:
Individual Consultation - Initial (upto 45 mins):
Individual Consultation - Review (upto 30 mins):

Concession-Individual Consultation -Initial (upto 45 mins):
Concession-Individual Consultation - Review (upto 30 mins):
Please Note: Concession applies for health care card holders & pensioners

Group Based Services: Pricing subject to the type of service provided. Please contact us for an obligation free quote.
Education Topics Include:
- Paediatric Nutrition (Introducing Solids, Fussy Eating, Healthy Eating)
- Pregnancy Nutrition, Gestational Diabetes, Breastfeeding/Lactation Nutrition
- Healthy Eating, Supermarket Shopping Tips, Nutrition Label Reading Tips, Healthier
sub heading under nutrition & diet:
-Vitacover:
--A rebate of $52.95 is available from Vitacover if an EPC ( Enhanced Primary Care)/Chronic Disease Management (CDM) plan is issued by your GP.
--All mandatory paperwork needs to be available at the time of making your appointment for your eligibility.
-Private Health Fund:
--Most private health funds provide rebate on dietetic appointments. However the rebate amount depends on your level of cover. Thus, please contact your health fund to determine your entitled rebate.
-RSB: Approved provider for RSB services

6) FOR DOCTORS: Bright Vale Paediatric Gastroenterologist Referral Form
Bright Vale Dietitian Referral form
7) LOCATIONS & CONTACT

Paediatric Gastroenterology & Hepatology Service
Suite 46
Holy Lantern Bramcote Medical Centre
17 Colin Ferris Pde,
MURDOCH, WA 6150
P: (08) 9422 5061
F: (08) 9422 3094

Nutrition & Diet Service
Suite 46
17 Colin Ferris Pde,
MURDOCH, WA 6150
P: (08) 9422 5061
F: (08) 9422 3094

Tolland Medical Centre
58-60 Karrigan Parkway,
MANDURAH, WA 6210
P: (08) 9647 2283
F: (08) 96724419
www.tmcexample.com.au

This page should have a webform that has following titles:
-Your Name
-Your Email
-Your Phone
-Message

8) NEWS & BLOG
Nice to have
• We liked the design style of the websites below:
https://www.vendoraplex.example/

http://qoravelt.example/

But feel free to use your creativity too
Should not have
• Please do not use any body building or muscle building images

```html
<!DOCTYPE html>
<html lang="en">
<head>
<meta charset="utf-8">
<title>Bright Vale – Location</title>
<link rel="stylesheet" href="https://fonts.googleapis.com/css2?family=Arimo:wght@400;700&display=swap">
<style>
  :root {
    --choc-dark: #5b3a22;
    --choc-panel: #7a5a47;
    --frame-light: #c9bbb1;
    --frame-mid: #b9a99e;
    --content-bg: #dcd4ce;
    --edge-white: #f4f1ee;
    --orange: #f7a23e;
    --lime: #d6e64a;
    --lime-soft: #e2ef6e;
    --heading-brown: #5a3517;
    --ink: #111111;
    --white: #ffffff;
  }
  * { box-sizing: border-box; margin: 0; padding: 0; }
  html, body { width: 1200px; height: 860px; overflow: hidden; }
  body {
    position: relative;
    font-family: "Arimo", Arial, sans-serif;
    color: var(--ink);
    background: var(--choc-dark);
  }
  .page-backdrop {
    position: absolute; inset: 0;
    background: radial-gradient(ellipse at center, #6a4630 0%, var(--choc-dark) 70%);
  }
  .site-frame {
    position: absolute; left: 35px; top: 37px; width: 1130px; height: 785px;
    border: 2px solid var(--edge-white); border-radius: 16px;
    background: linear-gradient(180deg, var(--frame-light) 0%, var(--frame-mid) 100%);
  }
  .account-links {
    position: absolute; left: 1024px; top: 45px;
    font-size: 13px; color: var(--choc-dark);
  }
  .account-links a { color: var(--choc-dark); }
  .account-links .divider { margin: 0 6px; color: #8b7565; }

  .site-header {
    position: absolute; left: 250px; top: 62px; width: 698px; height: 176px;
    background: var(--choc-panel);
    border: 3px solid var(--edge-white); border-radius: 20px;
    display: flex; align-items: center; justify-content: center; gap: 12px;
  }
  .brand-dot { width: 22px; height: 22px; border-radius: 50%; background: var(--orange); }
  .brand-name { font-size: 34px; font-weight: 700; color: var(--orange); letter-spacing: 1px; }

  .sidebar-block {
    position: absolute; background: var(--choc-panel);
    border: 3px solid var(--edge-white); border-radius: 8px;
  }
  .block-title {
    height: 28px; line-height: 26px; text-align: center;
    color: var(--white); font-weight: 700; font-size: 15px;
    border-bottom: 2px solid var(--edge-white);
  }
  .main-menu { left: 62px; top: 259px; width: 222px; height: 239px; }
  .main-menu ul { list-style: circle; color: #e9ddd3; margin: 22px 0 0 56px; }
  .main-menu li { font-size: 13px; line-height: 17.5px; font-weight: 700; }
  .main-menu a { color: var(--orange); }
  .main-menu a.visited { color: var(--lime); }

  .user-login { left: 915px; top: 259px; width: 222px; height: 210px; }
  .login-form { padding: 16px 0 0 15px; color: var(--white); font-size: 13px; font-weight: 700; }
  .login-form label { display: block; }
  .login-form .req { color: #d11; }
  .login-form input {
    width: 107px; height: 20px; margin: 1px 0 13px;
    border: 1px solid #999; font: 13px "Arimo", Arial, sans-serif; padding: 0 3px;
  }
  .login-form ul { list-style: disc; margin: -4px 0 0 21px; font-weight: 400; font-size: 12px; }
  .login-form ul a { color: var(--lime-soft); }
  .login-form button {
    margin-top: 13px; width: 52px; height: 19px; font: 12px "Arimo", Arial, sans-serif;
    background: linear-gradient(#fafafa, #dedede); border: 1px solid #888; border-radius: 2px;
  }

  .content-panel {
    position: absolute; left: 297px; top: 259px; width: 605px; height: 498px;
    background: var(--content-bg);
    border: 3px solid var(--edge-white); border-radius: 8px;
  }
  .breadcrumb {
    margin: 5px 9px 0 9px; padding: 0 0 3px 9px;
    font-size: 12px; font-weight: 700; border-bottom: 2px solid #b3a9a2;
  }
  .breadcrumb a { color: var(--ink); }
  .page-title { margin: 11px 0 0 9px; font-size: 20px; font-weight: 700; color: var(--heading-brown); }
  .locations { margin: 27px 0 0 22px; }
  .service-name { font-size: 14px; font-weight: 700; text-decoration: underline; line-height: 16px; }
  .address { font-size: 12px; font-weight: 700; line-height: 15.3px; font-style: normal; margin-bottom: 14px; }
  .address.plain { margin-top: 14px; }
  .site-link {
    display: inline-block; margin-top: -2px;
    font-size: 16px; font-weight: 700; color: var(--heading-brown);
  }
  .content-rule {
    position: absolute; left: 22px; top: 472px; width: 556px; height: 0;
    border-top: 2px solid #b3a9a2;
  }

  .site-footer {
    position: absolute; left: 0; top: 783px; width: 1200px; text-align: center;
    font-size: 12px; font-weight: 700;
  }
  .site-footer a { color: var(--ink); }
</style>
</head>
<body>
  <div class="page-backdrop" role="img" aria-label="Chocolate brown backdrop with a faint pattern of hand-drawn fruit and vegetables"></div>
  <div class="site-frame" role="img" aria-label="Light brown frame with faint fruit and vegetable pattern"></div>

  <nav class="account-links"><a href="#">Login</a><span class="divider">|</span><a href="#">Register</a></nav>

  <header class="site-header">
    <span class="brand-dot"></span>
    <span class="brand-name">Bright Vale</span>
  </header>

  <aside class="sidebar-block main-menu">
    <h2 class="block-title">Main menu</h2>
    <ul>
      <li><a href="#">Home</a></li>
      <li><a href="#">About Us</a></li>
      <li><a href="#">Nutrition &amp; Diet</a></li>
      <li><a href="#">Paediatric Gastroenterology</a></li>
      <li><a href="#">Fees &amp; Rebate</a></li>
      <li><a href="#">For Doctors</a></li>
      <li><a href="#">Location</a></li>
      <li><a class="visited" href="#">Contact</a></li>
      <li><a class="visited" href="#">News &amp; Blog</a></li>
    </ul>
  </aside>

  <main class="content-panel">
    <div class="breadcrumb"><a href="#">Home</a></div>
    <h1 class="page-title">Location</h1>
    <section class="locations">
      <h3 class="service-name">Paediatric Gastroenterology &amp; Hepatology Service</h3>
      <address class="address">Suite 46<br>Holy Lantern Bramcote Medical Centre<br>17 Colin Ferris Pde,<br>MURDOCH, WA 6150<br>P: (08) 9422 5061<br>F: (08) 9422 3094</address>
      <h3 class="service-name">Nutrition &amp; Diet Service</h3>
      <address class="address">Suite 46<br>Holy Lantern Bramcote Medical Centre<br>17 Colin Ferris Pde,<br>MURDOCH, WA 6150<br>P: (08) 9422 5061<br>F: (08) 9422 3094</address>
      <address class="address">Tolland Medical Centre<br>58-60 Karrigan Parkway,<br>MANDURAH, WA 6210<br>P: (08) 9647 2283<br>F: (08) 96724419</address>
      <a class="site-link" href="#">www.tmcexample.com.au</a>
    </section>
    <div class="content-rule"></div>
  </main>

  <aside class="sidebar-block user-login">
    <h2 class="block-title">User login</h2>
    <form class="login-form">
      <label for="user">Username <span class="req">*</span></label>
      <input id="user" type="text" value="Rowan">
      <label for="pass">Password <span class="req">*</span></label>
      <input id="pass" type="password" value="secretpass1">
      <ul><li><a href="#">Request new password</a></li></ul>
      <button type="button">Log in</button>
    </form>
  </aside>

  <footer class="site-footer"><a href="#">Bright Vale</a> © Copyright 2014</footer>
</body>
</html>
```